BildeVOLD buisnesscard

Hey :) I need a modern buisnesscard for my company BildeVOLD
It most have:
Dagligleder og Fotograf: Henrik Audun Strandvik

Mob: +4791264085
Epost: post@bildevold.example
Adresse: Kvernbakken9, 6040 Langevåg

Facbook and instagram logo with text BildeVOLD

BildeVOLD logo

It Company

```html
<!DOCTYPE html>
<html lang="no">
<head>
<meta charset="utf-8">
<title>BildeVOLD – visittkort</title>
<link rel="stylesheet" href="https://fonts.googleapis.com/css2?family=Didact+Gothic&display=swap">
<style>
  :root {
    --page: #ffffff;
    --card: #4a4a4c;
    --card-edge: #3a3a3c;
    --ink: #d1d2d4;
  }
  * { margin: 0; padding: 0; box-sizing: border-box; }
  html, body {
    width: 1014px; height: 1200px; overflow: hidden;
    background: var(--page);
    font-family: "Didact Gothic", sans-serif;
    color: var(--ink);
  }
  .card {
    position: absolute; left: 0; width: 1014px; height: 579px;
    background: var(--card);
    border: 1px solid var(--card-edge);
  }
  .card--front { top: 0; }
  .card--back { top: 621px; }
  .abs { position: absolute; white-space: nowrap; line-height: 1; }

  .brand-mark-small { position: absolute; left: 770px; top: 34px; width: 104px; height: 104px; background: var(--ink); }
  .brand-small { left: 670px; top: 150px; font-size: 58px; letter-spacing: 1px; }
  .holder-name { left: 84px; top: 214px; font-size: 37px; letter-spacing: 0.5px; }
  .holder-role { left: 144px; top: 280px; font-size: 30px; letter-spacing: 0.8px; }
  .contact { left: 156px; font-size: 36px; letter-spacing: 0.6px; }
  .contact--phone { top: 364px; font-size: 40px; letter-spacing: 1.5px; }
  .contact--mail { top: 440px; }
  .contact--addr { top: 507px; }
  .icon { position: absolute; }

  .brand-mark { position: absolute; left: 407px; top: 103px; width: 200px; height: 200px; background: var(--ink); }
  .brand-large { left: 0; width: 1014px; top: 318px; text-align: center; font-size: 112px; letter-spacing: 4px; }
  .social { top: 499px; font-size: 26px; letter-spacing: 0.5px; }
  .social--left { left: 132px; }
  .social--right { right: 154px; }
  .social-box { position: absolute; top: 483px; width: 56px; height: 56px; background: var(--ink); border-radius: 6px; }
  .social-box--left { left: 66px; }
  .social-box--right { left: 878px; }
</style>
</head>
<body>
  <section class="card card--front">
    <div class="brand-mark-small"></div>
    <div class="abs brand-small">BildeVOLD</div>
    <div class="abs holder-name">HENRIK AUDUN STRANDVIK</div>
    <div class="abs holder-role">Dagligleder og Fotograf</div>

    <svg class="icon" style="left:94px;top:349px" width="42" height="67" viewBox="0 0 42 67" fill="none" stroke="var(--ink)" stroke-width="3">
      <rect x="2" y="2" width="38" height="63" rx="5"/>
      <line x1="2" y1="10" x2="40" y2="10"/>
      <line x1="2" y1="54" x2="40" y2="54"/>
      <line x1="16" y1="6" x2="26" y2="6"/>
      <circle cx="21" cy="60" r="2" fill="var(--ink)"/>
    </svg>
    <div class="abs contact contact--phone">+479 126 4085</div>

    <svg class="icon" style="left:92px;top:444px" width="46" height="34" viewBox="0 0 46 34" fill="none" stroke="var(--ink)" stroke-width="3">
      <rect x="2" y="2" width="42" height="30"/>
      <polyline points="2,2 23,19 44,2"/>
      <line x1="2" y1="32" x2="18" y2="15"/>
      <line x1="44" y1="32" x2="28" y2="15"/>
    </svg>
    <div class="abs contact contact--mail">post@bildevold.example</div>

    <svg class="icon" style="left:96px;top:500px" width="38" height="44" viewBox="0 0 38 44" fill="none" stroke="var(--ink)" stroke-width="3">
      <path d="M19 42 C10 31 3 24 3 17 A16 16 0 0 1 35 17 C35 24 28 31 19 42 Z"/>
      <circle cx="19" cy="17" r="6"/>
    </svg>
    <div class="abs contact contact--addr">Kvernbakken 9, 6040 Fjordnes</div>
  </section>

  <section class="card card--back">
    <div class="brand-mark"></div>
    <div class="abs brand-large">BildeVOLD</div>

    <div class="social-box social-box--left"></div>
    <div class="abs social social--left">BildeVOLD</div>
    <div class="abs social social--right">BildeVOLD</div>
    <div class="social-box social-box--right"></div>
  </section>
</body>
</html>
```